Yearbook of one of our programs

Our company, Bluewater Circle, www.bluewatercircle.example, hosts leadership programs and workshops for women in leadership roles from different companies all around the world. We need a year book, 11 x 17 inches, we will print with a soft cover, and be approximately 70 pages. Due date for the final completion is 12/9. However, the initial contest & fee is only for pages 1-5, 26-27 and 40-41 (please see attached last year's version). We’d like to use the same color as that. Also attached is the outline we will use once a designer is selected. $50 hourly rate for the completion of the book is set once a designer is confirmed.

```html
<!DOCTYPE html>
<html lang="en">
<head>
<meta charset="utf-8">
<title>Bluewater Circle – Class of 2022 Members</title>
<link href="https://fonts.googleapis.com/css2?family=Dancing+Script:wght@600&family=Open+Sans:ital,wght@0,400;0,600;0,700;1,400&display=swap" rel="stylesheet">
<style>
  :root{
    --berry:#b52a5c;
    --berry-soft:#d98aa7;
    --ink:#3d3f4a;
    --text:#5a5a60;
    --paper:#ffffff;
    --desk:#e6e3e8;
    --photo-a:#cdb7a6;
    --photo-b:#8d7464;
    --floral:#f6e4ea;
  }
  *{box-sizing:border-box;margin:0;padding:0}
  html,body{width:1200px;height:789px;overflow:hidden;background:var(--desk)}
  body{font-family:"Open Sans",Arial,sans-serif;color:var(--text);position:relative}
  .spread{position:absolute;left:10px;top:10px;width:1180px;height:769px;display:flex}
  .page{position:relative;width:590px;height:769px;background:var(--paper);overflow:hidden}
  .page--left{box-shadow:inset -14px 0 18px -14px rgba(0,0,0,.18)}
  .page--right{box-shadow:inset 14px 0 18px -14px rgba(0,0,0,.18)}

  .title-banner{position:absolute;left:0;top:30px;width:340px;height:40px}
  .title-banner svg{position:absolute;inset:0}
  .title-banner h1{position:absolute;left:28px;top:3px;font-family:"Dancing Script",cursive;font-weight:600;font-size:27px;color:#fff;white-space:nowrap}

  .floral{position:absolute;right:0;top:60px;width:170px;height:190px;background:radial-gradient(circle at 60% 45%,var(--floral),rgba(255,255,255,0) 70%)}

  .row{position:absolute;left:0;width:590px;height:200px}
  .row-1{top:88px}.row-2{top:292px}.row-3{top:496px}
  .band{position:absolute;left:0;top:102px;width:560px;height:18px}
  .member{position:absolute;top:0;width:140px;text-align:center}
  .col-1{left:25px}.col-2{left:155px}.col-3{left:285px}.col-4{left:415px}
  .photo{width:100px;height:100px;margin:0 auto;border-radius:50%;border:3px solid var(--berry);padding:3px;background:#fff}
  .photo span{display:block;width:100%;height:100%;border-radius:50%;background:radial-gradient(circle at 50% 40%,var(--photo-a),var(--photo-b))}
  .name{height:18px;line-height:18px;margin-top:2px;color:#fff;font-weight:700;font-size:11.5px;white-space:nowrap;position:relative}
  .role{margin-top:4px;font-size:8.5px;line-height:11px;color:#333;white-space:nowrap}
  .company,.city{font-size:9px;line-height:11.5px;font-style:italic;white-space:nowrap}
  .status{font-size:9px;line-height:12px;font-weight:700;color:var(--berry);white-space:nowrap}

  .footer{position:absolute;left:0;bottom:0;width:590px;height:80px}
  .footer svg{position:absolute;inset:0}
  .footer .url{position:absolute;left:34px;top:12px;color:#fff;font-size:13px;white-space:nowrap}
  .footer .dot{display:inline-block;width:9px;height:9px;border-radius:50%;background:#fff;margin-right:10px;vertical-align:1px}
  .footer .folio{position:absolute;right:30px;top:40px;font-size:12px;letter-spacing:.5px;color:var(--berry-soft);white-space:nowrap}
  .footer .folio b{color:var(--ink);font-weight:600;margin-left:6px;padding-left:8px;border-left:1px solid var(--berry-soft)}
</style>
</head>
<body>
<main class="spread">

  <section class="page page--left">
    <header class="title-banner">
      <svg width="340" height="40"><polygon points="0,4 300,4 285,36 0,36" fill="var(--berry)"/><line x1="318" y1="2" x2="298" y2="38" stroke="var(--ink)" stroke-width="3"/></svg>
      <h1>Class of 2022 Members</h1>
    </header>
    <div class="floral" role="img" aria-label="Faint floral line ornament"></div>

    <div class="row row-1">
      <svg class="band"><polygon points="0,0 560,0 548,18 0,18" fill="var(--berry)"/></svg>
      <article class="member col-1"><div class="photo" role="img" aria-label="Portrait photo of Nora Castell"><span></span></div><div class="name">Nora Castell</div><p class="role">VP, Specialty Solutions</p><p class="company">Hallmere Health</p><p class="city">Bloomfield, CT</p><p class="status">Member, 2021 and 2022</p></article>
      <article class="member col-2"><div class="photo" role="img" aria-label="Portrait photo of Lena Harwick"><span></span></div><div class="name">Lena Harwick</div><p class="role">VP, Finance - Infrastructure</p><p class="company">Voltaris</p><p class="city">Dublin, Ireland</p><p class="status">Founding Member, 2010-2022</p></article>
      <article class="member col-3"><div class="photo" role="img" aria-label="Portrait photo of Danielle Okoro"><span></span></div><div class="name">Danielle Okoro</div><p class="role">President, Global Supply Chain</p><p class="company">Prairie Grain Works</p><p class="city">Union, KY</p><p class="status">New Member 2022</p></article>
      <article class="member col-4"><div class="photo" role="img" aria-label="Portrait photo of Kara Lindqvist"><span></span></div><div class="name">Kara Lindqvist</div><p class="role">GM, Halden Performance<br>Films Business</p><p class="company">Halden</p><p class="city">St. Louis, MO</p><p class="status">New Member 2022</p></article>
    </div>

    <div class="row row-2">
      <svg class="band"><polygon points="0,0 560,0 548,18 0,18" fill="var(--berry)"/></svg>
      <article class="member col-1"><div class="photo" role="img" aria-label="Portrait photo of Mariana Telles dos"><span></span></div><div class="name">Mariana Telles dos</div><p class="role">EVP Operations, Supply &amp; Quality</p><p class="company">Enzora</p><p class="city">Skodsborg, Denmark</p><p class="status">New Member, 2022</p></article>
      <article class="member col-2"><div class="photo" role="img" aria-label="Portrait photo of Hannah Whitlock"><span></span></div><div class="name">Hannah Whitlock</div><p class="role">SVP, Life Underwriting<br>and New Business</p><p class="company">Granite Life Corporation</p><p class="city">Greensboro, NC</p><p class="status">Founding Member, 2019-2022</p></article>
      <article class="member col-3"><div class="photo" role="img" aria-label="Portrait photo of Tess Marlow"><span></span></div><div class="name">Tess Marlow</div><p class="role">CFO</p><p class="company">Harbor Row Capital</p><p class="city">Baltimore, MD</p><p class="status">New Member 2022</p></article>
      <article class="member col-4"><div class="photo" role="img" aria-label="Portrait photo of Julia Brennan"><span></span></div><div class="name">Julia Brennan</div><p class="role">VP and GM, North America<br>&amp; Global Outdoor, Ridgeline</p><p class="company">Stitchline Brands, Inc.</p><p class="city">Greensboro, NC</p><p class="status">New Member 2022</p></article>
    </div>

    <div class="row row-3">
      <svg class="band"><polygon points="0,0 560,0 548,18 0,18" fill="var(--berry)"/></svg>
      <article class="member col-1"><div class="photo" role="img" aria-label="Portrait photo of Amy Lien"><span></span></div><div class="name">Amy Lien</div><p class="role">CFO of North America</p><p class="company">Tallowmark Supply</p><p class="city">St. Louis, MO</p><p class="status">Founding Member, 2019-2022</p></article>
      <article class="member col-2"><div class="photo" role="img" aria-label="Portrait photo of Rae Ellison"><span></span></div><div class="name">Rae Ellison</div><p class="role">Chief Information Officer,<br>Northway Investment<br>Management Technology</p><p class="company">Northway</p><p class="city">Boston, MA</p><p class="status">New Member, 2022</p></article>
      <article class="member col-3"><div class="photo" role="img" aria-label="Portrait photo of Lucia Ferreira"><span></span></div><div class="name">Lucia Ferreira</div><p class="role">President, Global Specialty<br>Ingredients</p><p class="company">Prairie Grain Works</p><p class="city">Chicago, IL</p><p class="status">Founding Member, 2019-2022</p></article>
      <article class="member col-4"><div class="photo" role="img" aria-label="Portrait photo of Paula Reyes"><span></span></div><div class="name">Paula Reyes</div><p class="role">SVP, Finance</p><p class="company">Quillstream Works</p><p class="city">San Jose, CA</p><p class="status">New Member 2022</p></article>
    </div>

    <footer class="footer">
      <svg width="590" height="80"><polygon points="0,6 300,6 285,36 0,36" fill="var(--berry)"/><polyline points="318,6 300,42 590,42" fill="none" stroke="var(--ink)" stroke-width="3"/></svg>
      <p class="url"><span class="dot"></span>www.bluewatercircle.example</p>
      <p class="folio">BLUEWATER TIDE<b>04</b></p>
    </footer>
  </section>

  <section class="page page--right">
    <header class="title-banner">
      <svg width="340" height="40"><polygon points="0,4 300,4 285,36 0,36" fill="var(--berry)"/><line x1="318" y1="2" x2="298" y2="38" stroke="var(--ink)" stroke-width="3"/></svg>
      <h1>Class of 2022 Members</h1>
    </header>
    <div class="floral" role="img" aria-label="Faint floral line ornament"></div>

    <div class="row row-1">
      <svg class="band"><polygon points="0,0 560,0 548,18 0,18" fill="var(--berry)"/></svg>
      <article class="member col-1"><div class="photo" role="img" aria-label="Portrait photo of Nora Castell"><span></span></div><div class="name">Nora Castell</div><p class="role">VP, Specialty Solutions</p><p class="company">Hallmere Health</p><p class="city">Bloomfield, CT</p><p class="status">Member, 2021 and 2022</p></article>
      <article class="member col-2"><div class="photo" role="img" aria-label="Portrait photo of Lena Harwick"><span></span></div><div class="name">Lena Harwick</div><p class="role">VP, Finance - Infrastructure</p><p class="company">Voltaris</p><p class="city">Dublin, Ireland</p><p class="status">Founding Member, 2010-2022</p></article>
      <article class="member col-3"><div class="photo" role="img" aria-label="Portrait photo of Danielle Okoro"><span></span></div><div class="name">Danielle Okoro</div><p class="role">President, Global Supply Chain</p><p class="company">Prairie Grain Works</p><p class="city">Union, KY</p><p class="status">New Member 2022</p></article>
      <article class="member col-4"><div class="photo" role="img" aria-label="Portrait photo of Kara Lindqvist"><span></span></div><div class="name">Kara Lindqvist</div><p class="role">GM, Halden Performance<br>Films Business</p><p class="company">Halden</p><p class="city">St. Louis, MO</p><p class="status">New Member 2022</p></article>
    </div>

    <div class="row row-2">
      <svg class="band"><polygon points="0,0 560,0 548,18 0,18" fill="var(--berry)"/></svg>
      <article class="member col-1"><div class="photo" role="img" aria-label="Portrait photo of Mariana Telles dos"><span></span></div><div class="name">Mariana Telles dos</div><p class="role">EVP Operations, Supply &amp; Quality</p><p class="company">Enzora</p><p class="city">Skodsborg, Denmark</p><p class="status">New Member, 2022</p></article>
      <article class="member col-2"><div class="photo" role="img" aria-label="Portrait photo of Hannah Whitlock"><span></span></div><div class="name">Hannah Whitlock</div><p class="role">SVP, Life Underwriting<br>and New Business</p><p class="company">Granite Life Corporation</p><p class="city">Greensboro, NC</p><p class="status">Founding Member, 2019-2022</p></article>
      <article class="member col-3"><div class="photo" role="img" aria-label="Portrait photo of Tess Marlow"><span></span></div><div class="name">Tess Marlow</div><p class="role">CFO</p><p class="company">Harbor Row Capital</p><p class="city">Baltimore, MD</p><p class="status">New Member 2022</p></article>
      <article class="member col-4"><div class="photo" role="img" aria-label="Portrait photo of Julia Brennan"><span></span></div><div class="name">Julia Brennan</div><p class="role">VP and GM, North America<br>&amp; Global Outdoor, Ridgeline</p><p class="company">Stitchline Brands, Inc.</p><p class="city">Greensboro, NC</p><p class="status">New Member 2022</p></article>
    </div>

    <div class="row row-3">
      <svg class="band"><polygon points="0,0 560,0 548,18 0,18" fill="var(--berry)"/></svg>
      <article class="member col-1"><div class="photo" role="img" aria-label="Portrait photo of Amy Lien"><span></span></div><div class="name">Amy Lien</div><p class="role">CFO of North America</p><p class="company">Tallowmark Supply</p><p class="city">St. Louis, MO</p><p class="status">Founding Member, 2019-2022</p></article>
      <article class="member col-2"><div class="photo" role="img" aria-label="Portrait photo of Rae Ellison"><span></span></div><div class="name">Rae Ellison</div><p class="role">Chief Information Officer,<br>Northway Investment<br>Management Technology</p><p class="company">Northway</p><p class="city">Boston, MA</p><p class="status">New Member, 2022</p></article>
      <article class="member col-3"><div class="photo" role="img" aria-label="Portrait photo of Lucia Ferreira"><span></span></div><div class="name">Lucia Ferreira</div><p class="role">President, Global Specialty<br>Ingredients</p><p class="company">Prairie Grain Works</p><p class="city">Chicago, IL</p><p class="status">Founding Member, 2019-2022</p></article>
      <article class="member col-4"><div class="photo" role="img" aria-label="Portrait photo of Paula Reyes"><span></span></div><div class="name">Paula Reyes</div><p class="role">SVP, Finance</p><p class="company">Quillstream Works</p><p class="city">San Jose, CA</p><p class="status">New Member 2022</p></article>
    </div>

    <footer class="footer">
      <svg width="590" height="80"><polygon points="0,6 300,6 285,36 0,36" fill="var(--berry)"/><polyline points="318,6 300,42 590,42" fill="none" stroke="var(--ink)" stroke-width="3"/></svg>
      <p class="url"><span class="dot"></span>www.bluewatercircle.example</p>
      <p class="folio">BLUEWATER TIDE<b>05</b></p>
    </footer>
  </section>

</main>
</body>
</html>
```